sydney wedding photography business needs a business card design

we need a business card design for a sydney based wedding photography and videography business. our business name is :golden hour studio and film. our target clients are 24-35 yrs female. our style is candid, organic, natural, dynamic. we are a team of young photographers and videographers, and help brides to create memories that they will cherish for the rest of their lives. the logo will be provided. we want an elegant design that reflects our style, and also want to give a great impression to our clients that we are one of the best studios in sydney and our brand means quality and premium service.

Target Market(s)

bride to be, 24-35 years old, living in sydney and surrunding areas

Industry/Entity Type

Wedding Photography

Contact Information for Business Card

address: 57 tarrant street, glenmore nsw 2047
mobile: 0431872259
phone: (02) 9163 2408
info@tidewillowstudio.net.au
www.tidewillowstudio.net.au
facebook:tidewillowweddings
instagram:tidewillowweddings

Font styles to use
Serif
Sans Serif

Requirements
Nice to have
• maybe add my slogan"memories beyond eternity" if the layout looks good
Should not have
• no black color, not good idea for wedding biz card

```html
<!DOCTYPE html>
<html lang="en">
<head>
<meta charset="utf-8">
<title>Golden Hour Studio and Film – Business Card</title>
<link href="https://fonts.googleapis.com/css2?family=Open+Sans:wght@400;600;700&display=swap" rel="stylesheet">
<style>
  :root {
    --page-bg: #ece9e4;
    --gold-top: #b8861c;
    --gold-bottom: #f4c302;
    --gold-text: #e6ae14;
    --ink: #2a2118;
    --card-back: #4a3a26;
    --card-back-deep: #3b2e1f;
    --art-shade: rgba(120, 80, 10, 0.22);
  }
  * { box-sizing: border-box; margin: 0; padding: 0; }
  html, body { width: 1200px; height: 900px; overflow: hidden; }
  body {
    position: relative;
    background: var(--page-bg);
    font-family: "Open Sans", Arial, sans-serif;
    color: var(--ink);
  }
  .card {
    position: absolute;
    height: 343px;
    box-shadow: 0 6px 18px rgba(0,0,0,0.18);
    overflow: hidden;
  }
  .card--front {
    left: 238px; top: 62px;
    width: 556px;
    background: linear-gradient(180deg, var(--gold-top) 0%, var(--gold-bottom) 100%);
  }
  .card--back {
    left: 459px; top: 518px;
    width: 560px;
    background: radial-gradient(ellipse at center, var(--card-back) 0%, var(--card-back-deep) 100%);
  }
  .brand-name {
    position: absolute;
    font-weight: 700;
    text-transform: uppercase;
    white-space: nowrap;
  }
  .card--front .brand-name {
    left: 40px; top: 46px;
    font-size: 14px;
    letter-spacing: 0.06em;
    color: var(--ink);
  }
  .card--back .brand-name {
    left: 0; right: 0; top: 152px;
    text-align: center;
    font-size: 24px;
    letter-spacing: 0.08em;
    color: var(--gold-text);
  }
  .person { position: absolute; left: 35px; top: 115px; }
  .person__name { font-size: 18px; font-weight: 700; line-height: 24px; }
  .person__role { font-size: 14.5px; line-height: 20px; }
  .address {
    position: absolute;
    left: 35px; top: 195px;
    font-size: 14.5px;
    line-height: 20px;
  }
  .contact-list {
    position: absolute;
    left: 35px; top: 249px;
    list-style: none;
    font-size: 14.5px;
    line-height: 20px;
  }
  .contact-list li { display: flex; align-items: center; gap: 8px; }
  .contact-list svg { width: 12px; height: 12px; flex: none; }
  .icon-fill { fill: var(--ink); }
  .icon-line { fill: none; stroke: var(--ink); stroke-width: 2.4; }
  .feature-art {
    position: absolute;
    left: 268px; top: 0;
    width: 288px; height: 343px;
    background: radial-gradient(ellipse at 75% 35%, var(--art-shade) 0%, rgba(120, 80, 10, 0) 70%);
  }
</style>
</head>
<body>
  <section class="card card--front">
    <div class="brand-name">Golden Hour Studio and Film</div>

    <div class="person">
      <div class="person__name">Mara Ellison</div>
      <div class="person__role">Managing Director</div>
    </div>

    <div class="address">57 Tarrant Street,<br>Glenmore NSW 2047</div>

    <ul class="contact-list">
      <li>
        <svg viewBox="0 0 24 24" aria-hidden="true"><path class="icon-fill" d="M6.6 10.8a15 15 0 0 0 6.6 6.6l2.2-2.2a1 1 0 0 1 1-.25 11.4 11.4 0 0 0 3.6.57 1 1 0 0 1 1 1V20a1 1 0 0 1-1 1A17 17 0 0 1 3 4a1 1 0 0 1 1-1h3.5a1 1 0 0 1 1 1c0 1.25.2 2.45.57 3.57a1 1 0 0 1-.25 1z"/></svg>
        0431872259
      </li>
      <li>
        <svg viewBox="0 0 24 24" aria-hidden="true"><rect class="icon-line" x="2.5" y="5.5" width="19" height="13"/><path class="icon-line" d="M2.5 5.5l9.5 7.5 9.5-7.5"/></svg>
        info@tidewillowstudio.net.au
      </li>
      <li>
        <svg viewBox="0 0 24 24" aria-hidden="true"><circle class="icon-line" cx="12" cy="12" r="9.5"/><path class="icon-line" d="M2.5 12h19M12 2.5c3 3 3 16 0 19M12 2.5c-3 3-3 16 0 19"/></svg>
        www.tidewillowstudio.net.au
      </li>
    </ul>

    <div class="feature-art" role="img" aria-label="Large outlined gem illustration in dark lines on gold"></div>
  </section>

  <section class="card card--back">
    <div class="brand-name">Golden Hour Studio and Film</div>
  </section>
</body>
</html>
```